Kelvara Pane Works Business Card

We need a business card design that is suitable for a Glazing Business. We Specialize in Repairing broken windows and doors and are a 24hr on call service. We manufacture Shower screens, Fly screens, Wardrobe doors, Security doors and grilles + mirrors. We stock a variety of mesh including Standard mesh, Pet resistant mesh, Tressmet & Clearweft. We would like to use a combination of Light Blue, Dark Blue, Black & White with perhaps a picture of glass breaking.

Industry/Entity Type

Business

Contact Information for Business Card

Narooma Glass Service60B Glasshouse Rocks RdNarooma NSW 2546PH / FAX - 02 44765210MOB - 0419682350 Andrewemail - kelvarapane@fenmail.example

Font styles to use
Serif

Colors
34a7d8
0255a3
ffffff

Requirements
Must have
• logo with picture of broken or cracked glass

```html
<!DOCTYPE html>
<html lang="en">
<head>
<meta charset="utf-8">
<title>Kelvara Pane Works – Business Card</title>
<link rel="stylesheet" href="https://fonts.googleapis.com/css2?family=Lato:wght@400;700&family=Oswald:wght@500&display=swap">
<style>
  :root {
    --stage-top: #2a2a2a;
    --stage-bottom: #050505;
    --card-white: #ffffff;
    --sky-blue: #78b0e0;
    --ink-grey: #3a3a3a;
    --text-dark: #333333;
    --rule-grey: #d6d6d6;
  }
  * { margin: 0; padding: 0; box-sizing: border-box; }
  html, body { width: 1200px; height: 900px; overflow: hidden; }
  body {
    position: relative;
    background: linear-gradient(180deg, var(--stage-top) 0%, var(--stage-bottom) 100%);
    font-family: "Lato", Arial, sans-serif;
  }
  .card {
    position: absolute;
    top: 306px;
    width: 440px;
    height: 271px;
    border-radius: 12px;
    overflow: hidden;
    background: var(--card-white);
  }
  .card--front { left: 149px; }
  .card--back { left: 608px; }

  .band { position: absolute; left: 0; width: 100%; background: var(--sky-blue); }
  .card--front .band { top: 0; height: 92px; }
  .card--back .band { top: 174px; bottom: 0; }

  .holder-name {
    position: absolute; left: 29px; top: 15px;
    font-family: "Oswald", Arial, sans-serif; font-weight: 500;
    font-size: 20px; letter-spacing: 0.5px; color: var(--card-white);
  }
  .email {
    position: absolute; right: 13px; top: 17px;
    font-size: 12.5px; color: var(--card-white);
  }
  .emblem {
    position: absolute; border-radius: 50%;
    background: var(--sky-blue);
    display: flex; align-items: center; justify-content: center; text-align: center;
  }
  .card--front .emblem {
    left: 147px; top: 32px; width: 120px; height: 120px;
    border: 5px solid var(--ink-grey);
    box-shadow: 0 0 0 5px var(--card-white);
    font-weight: 700; font-size: 14px; line-height: 1.25; color: var(--card-white);
    padding: 0 14px;
  }
  .phones {
    position: absolute; top: 164px; left: 0; width: 100%; height: 40px;
    font-size: 13.5px; color: var(--text-dark);
  }
  .phones .mobile { position: absolute; right: 235px; top: 11px; display: flex; align-items: center; gap: 8px; }
  .phones .office { position: absolute; left: 230px; top: 11px; display: flex; align-items: center; gap: 8px; }
  .phones .divider { position: absolute; left: 215px; top: 0; width: 1px; height: 40px; background: var(--rule-grey); }
  .address {
    position: absolute; top: 222px; width: 100%; text-align: center;
    font-size: 13px; color: var(--sky-blue);
  }

  .lockup {
    position: absolute; left: 80px; top: 42px;
    display: flex; align-items: center; gap: 10px;
  }
  .lockup .mark {
    width: 86px; height: 86px; border-radius: 50%;
    border: 4px solid var(--ink-grey); background: var(--sky-blue);
  }
  .lockup .brand {
    font-weight: 700; font-size: 24px; line-height: 1.2; letter-spacing: 1.5px;
    color: var(--ink-grey); text-transform: uppercase;
  }
  .services {
    position: absolute; left: 0; top: 206px; width: 100%; text-align: center;
    font-size: 14px; line-height: 18px; color: var(--card-white);
  }
</style>
</head>
<body>
  <section class="card card--front" aria-label="Business card front">
    <div class="band" role="img" aria-label="Light blue band with faint shattered glass texture"></div>
    <p class="holder-name">MALCOLM</p>
    <p class="email">kelvarapane@fenmail.example</p>
    <div class="emblem">Kelvara Pane Works</div>
    <div class="phones">
      <span class="mobile">0419682350
        <svg width="8" height="12" viewBox="0 0 8 12" aria-hidden="true"><rect x="0.75" y="0.75" width="6.5" height="10.5" rx="1.2" fill="none" stroke="#78b0e0" stroke-width="1.5"/></svg>
      </span>
      <span class="divider"></span>
      <span class="office">
        <svg width="11" height="10" viewBox="0 0 11 10" aria-hidden="true"><rect x="0" y="3" width="11" height="7" rx="1" fill="#78b0e0"/><rect x="2" y="0" width="7" height="4" rx="1" fill="#78b0e0"/></svg>
        02 48931067</span>
    </div>
    <p class="address">17C Tindale Ridge Rd Wyrrabee NSW 2719</p>
  </section>

  <section class="card card--back" aria-label="Business card back">
    <div class="lockup">
      <div class="mark"></div>
      <p class="brand">Kelvara<br>Pane Works</p>
    </div>
    <div class="band" role="img" aria-label="Light blue band with faint shattered glass texture"></div>
    <p class="services">Shower screens | Fly screens | Wardrobe doors<br>Security doors and grilles + mirrors</p>
  </section>
</body>
</html>
```